Keystonery Billboard - Financial Services Company (Investments, Tax Planning and Insurance)

Our new office has a billboard directly above the office building. We'd like something eye-catching with a strong Call to Action, with the main part of the billboard being under 7 words if possible. We'd like you to include a way to get ahold of us (either our website keystoneryllc.example or our phone number 302-418-2907. You may also include in small font something to indicate that we've been serving the area since 1980 (the DE area, the tri-state area, the Marlowe Hollow, etc.)

We offer financial planning, tax planning, and insurance, and we help our clients to focus on their goals and happiness by providing everything they need for lifelong wealth under one roof.

Our logos are attached, we use a triangle logo with green and gray. We use the tagline "discover lasting prosperity" but this does not need to be included.

Potential ideas we have seen from other financial companies-
- the concept that the driver spends more time looking at billboards than planning for their retirement
-something along the lines of "everything you need for your finances is in this building right here" planning, investments, taxes, insurance"
-don't spend your time worrying about retirement, let us help you plan for it
-are you working for your money, or is it working for you?
- retirement takes planning, we're here to help
- ready to retire? talk to us
- need investment advice?
- need help investing?
- crossing your fingers isn't a retirement plan. we can help.
- retiring soon? you need help.

Those are just general ideas, please feel free to be creative.

brand colors:
#00b585
#00b185
#000000
#ffffff
#6d6f75
#6d6f75
#6f7074
#021712
#052e24

```html
<!DOCTYPE html>
<html lang="en">
<head>
<meta charset="UTF-8">
<title>Keystonery Billboard</title>
<link rel="stylesheet" href="https://fonts.googleapis.com/css2?family=Anton&family=Oswald:wght@400;600&display=swap">
<style>
  :root {
    --canvas: #e9eaec;
    --board: #fbfaf6;
    --green: #168a3e;
    --slate: #33363b;
    --ink: #0d0f10;
    --band: #4a4d52;
    --white: #ffffff;
    --photo-light: #eef0f1;
    --photo-mid: #b9c3c8;
    --photo-dark: #4f5e66;
  }
  * { margin: 0; padding: 0; box-sizing: border-box; }
  html, body { width: 1200px; height: 800px; overflow: hidden; background: var(--canvas); }
  .billboard {
    position: absolute; left: 40px; top: 160px;
    width: 1120px; height: 480px;
    background: var(--board);
    box-shadow: 0 8px 28px rgba(0,0,0,.12);
    overflow: hidden;
  }
  .billboard-art { position: absolute; inset: 0; }
  .brand {
    position: absolute; left: 0; width: 520px; top: 46px;
    text-align: center;
  }
  .brand-name {
    display: inline-flex; align-items: center; gap: 10px;
    font-family: 'Oswald', sans-serif; font-weight: 600;
    font-size: 32px; letter-spacing: 1px; color: var(--green);
    white-space: nowrap;
  }
  .brand-mark { width: 15px; height: 15px; background: var(--slate); }
  .brand-tagline {
    font-family: 'Oswald', sans-serif; font-weight: 400;
    font-size: 10px; letter-spacing: 3px; text-transform: uppercase;
    color: var(--slate); margin-top: 2px; white-space: nowrap;
  }
  .headline {
    position: absolute; left: 0; width: 520px; top: 138px;
    text-align: center;
    font-family: 'Anton', sans-serif; font-weight: 400; text-transform: uppercase;
    line-height: 1.08;
  }
  .headline-line { display: block; font-size: 62px; letter-spacing: .5px; white-space: nowrap; }
  .headline-line--green { color: var(--green); }
  .headline-line--slate { color: var(--slate); }
  .headline-cta {
    display: inline-flex; align-items: center; gap: 18px;
    font-size: 76px; color: var(--ink); margin-top: 4px; white-space: nowrap;
  }
  .cta-dot { width: 14px; height: 14px; border-radius: 50%; background: var(--green); }
  .since {
    position: absolute; right: 44px; top: 30px;
    font-family: 'Oswald', sans-serif; font-weight: 600;
    font-size: 22px; letter-spacing: 2px; color: var(--white);
    white-space: nowrap;
  }
  .contact {
    position: absolute; left: 600px; right: 36px; bottom: 0; height: 66px;
    display: flex; align-items: center; justify-content: space-between; gap: 24px;
    font-family: 'Oswald', sans-serif; font-weight: 600;
    font-size: 21px; letter-spacing: 1px; color: var(--white);
  }
  .contact-item { display: inline-flex; align-items: center; gap: 10px; white-space: nowrap; flex-shrink: 0; }
  .contact-item--web { text-transform: uppercase; }
  .contact-icon { width: 20px; height: 20px; flex-shrink: 0; }
</style>
</head>
<body>
  <section class="billboard">
    <svg class="billboard-art" viewBox="0 0 1120 480" width="1120" height="480">
      <defs>
        <linearGradient id="photoTone" x1="0" y1="0" x2="1" y2="1">
          <stop offset="0" stop-color="var(--photo-light)"/>
          <stop offset=".55" stop-color="var(--photo-mid)"/>
          <stop offset="1" stop-color="var(--photo-dark)"/>
        </linearGradient>
        <clipPath id="photoShape">
          <path d="M600 0 L1120 0 L1120 480 L550 480 Q490 240 600 0 Z"/>
        </clipPath>
      </defs>
      <g clip-path="url(#photoShape)">
        <rect x="480" y="0" width="640" height="480" fill="url(#photoTone)" role="img" aria-label="Photo of two people reviewing financial charts on a tablet and calculator"/>
        <rect x="480" y="414" width="640" height="66" fill="var(--band)"/>
      </g>
    </svg>

    <div class="brand">
      <div class="brand-name"><span class="brand-mark"></span>Keystonery</div>
      <div class="brand-tagline">discover lasting prosperity</div>
    </div>

    <h1 class="headline">
      <span class="headline-line headline-line--green">Minimize Stress</span>
      <span class="headline-line headline-line--slate">Maximize Wealth</span>
      <span class="headline-cta"><span class="cta-dot"></span>Choose Us<span class="cta-dot"></span></span>
    </h1>

    <div class="since">SINCE 1980</div>

    <div class="contact">
      <span class="contact-item">
        <svg class="contact-icon" viewBox="0 0 24 24">
          <circle cx="12" cy="12" r="11" fill="var(--white)"/>
          <path d="M8.5 6.5l2 2-1.2 1.5c.8 1.8 2.2 3.2 4 4l1.5-1.2 2 2-1.3 1.7c-4.3-.6-8-4.3-8.6-8.6z" fill="var(--band)"/>
        </svg>
        302-418-2907
      </span>
      <span class="contact-item contact-item--web">
        <svg class="contact-icon" viewBox="0 0 24 24" fill="none" stroke="var(--white)" stroke-width="1.6">
          <circle cx="12" cy="12" r="10"/>
          <ellipse cx="12" cy="12" rx="4.5" ry="10"/>
          <line x1="2" y1="12" x2="22" y2="12"/>
          <path d="M4 7h16M4 17h16"/>
        </svg>
        www.keystoneryllc.example
      </span>
    </div>
  </section>
</body>
</html>
```